Redo our website for our Robotics company

We sell robotic equipment to the restaurant industry. Our current robot, is a cooking robot that cooks up to 15 lbs of food. We will provide a prior website as well as brand guidelines. We plan on using wordpress and take advantage of wordpress's visual (no code) editor.

Current website - https://kelvatrix88.com/ (please note we are only selling Tammo now and no longer selling Plavo+

We want someone to take our existing content and design the website as well as layout our content we provide. Here's a suggested site layout:

✅ KelvaTrix88 Website Wireframe / Site Map
1. Home

Purpose: Introduce Tammo, establish credibility, drive demo requests.

Sections:

Hero Section

Headline: “Meet Tammo — Your New Robotic Chef for High-Volume, Consistent Cooking.”

Sub-headline: Increase throughput. Reduce labor. Deliver perfect food every time.

CTA: Request a Demo + Watch Tammo Cook

Visual: Video loop or hero animation of Tammo in action.

How Tammo Works (3-4 steps)

Step cards: Load Ingredients → Select Recipe → Tammo Cooks → Serve

Icons and short explanations.

Key Benefits

Labor savings

Zero inconsistency

24/7 uptime

Throughput increases (30–50% faster)

Health & safety compliance

Who It’s For

QSR restaurants

Fast casual

Catering/commissaries

Ghost kitchens

Case Studies / Testimonials

Logo bar + quotes

“Tammo helped us reduce cooking times by 40%.”

Video Section

“Watch Tammo cook a full batch from start to finish.”

CTA Section

Big banner: Book a Demo

2. Product: “Meet Tammo”

Purpose: Deep dive into hardware, software, safety, reliability.

Sections:

Overview

What Tammo is

What tasks it automates

Where it fits in a kitchen

Hardware Features

High-temperature cooking chamber

Precision sensors

Automated stirring

Automated dispensing

Safety mechanisms (locking lids, auto-shutoff)

Software & AI

Recipe automation

IoT dashboard

Remote monitoring

Predictive maintenance

Specs Table

Dimensions

Power requirements

Capacity (lbs per batch)

Safety certifications

Gallery

Close-ups, installation photos, process shots

CTA: Request a Demo

3. Solutions

Purpose: Show that Tammo solves real operational problems.

Sub-pages or sections:

For Quick-Service Restaurants

Reduce labor cost

Speed up peak-hour demand

For Catering & Commissaries

Large-batch consistency

Automate repetitive cooking tasks

For High-Growth Chains

Replicable quality across multiple locations

Centralized recipe control

Each solution page includes:

A problem statement

How Tammo solves it

Metrics / KPIs

Relevant testimonial

CTA

4. ROI / Economics

Purpose: Sell the financial story clearly.

Sections:

Savings Calculator

Labor hours saved

Cost savings

Throughput increases

Food waste reduction

Before & After Comparison

Traditional kitchen vs. robotic kitchen

Sample ROI

“Payback in as little as 3–6 months.”

Download Full ROI Report (PDF)

5. Case Studies

Purpose: Social proof + real results.

Structure for each case study:

Customer background

Problem

Implementation

KPIs achieved

Labor savings

Consistency improvements

Cooking speed

Quote + photos/video

6. Pricing

Purpose: Start a commercial conversation.

Include:

Subscription model (monthly / annual)

Hardware leasing or purchase options

Installation + training

Support level

CTA to book a sales call

7. About

Purpose: Build trust.

Sections:

Mission statement

Founding team

Advisors/partners

“Why we built Tammo”

8. Resources

Purpose: SEO + education.

Subpages:

Blog (e.g., “The Future of Automated Kitchens”)

Whitepapers

Technical documentation

Product videos

9. Contact

General inquiry form

Sales contact

Support portal

Careers

```html
<!DOCTYPE html>
<html lang="en">
<head>
<meta charset="utf-8">
<title>KelvaTrix88 — Meet Tammo</title>
<link href="https://fonts.googleapis.com/css2?family=Poppins:ital,wght@0,400;0,500;0,600;0,700;1,400&display=swap" rel="stylesheet">
<style>
:root{
  --bg:#161616;
  --panel:#222222;
  --panel-2:#1c1c1c;
  --orange:#f26a21;
  --orange-deep:#e2461a;
  --text:#ffffff;
  --muted:#cfcfcf;
  --line:#3a3a3a;
}
*{margin:0;padding:0;box-sizing:border-box}
html,body{width:1200px;height:4781px;overflow:hidden;background:var(--bg);color:var(--text);font-family:'Poppins',sans-serif}
.page{position:relative;width:1200px;height:4781px;overflow:hidden}
.abs{position:absolute}
a{color:inherit;text-decoration:none}

/* nav */
.nav{position:absolute;top:0;left:0;width:1200px;height:104px;display:flex;align-items:center;font-size:14px;font-weight:500;letter-spacing:.3px}
.nav a{position:absolute;top:42px}
.nav .active{background:var(--orange);padding:4px 22px;transform:skewX(-14deg);left:68px;top:38px}
.nav .active span{display:inline-block;transform:skewX(14deg)}
.brand{display:flex;align-items:center;gap:8px;font-weight:700;font-size:26px;color:var(--text)}
.brand .mark{width:14px;height:14px;background:var(--orange)}

/* hero */
.hero-photo{left:0;top:104px;width:1200px;height:612px;border-radius:0 60px 0 110px;background:radial-gradient(ellipse at 60% 40%,#6b6660 0%,#3d3a37 45%,#1f1d1c 100%)}
.hero-card{left:115px;top:167px;width:970px;height:475px;background:rgba(40,38,36,.55);border-radius:16px}
.hero-title{left:0;width:1200px;top:228px;text-align:center;font-weight:700;font-size:56px;line-height:1.1}
.hero-sub{left:0;width:1200px;top:303px;text-align:center;font-weight:700;font-size:40px;line-height:60px}
.hero-lead{left:0;width:1200px;top:457px;text-align:center;font-size:17px;font-weight:500}
.btn{display:inline-flex;align-items:center;justify-content:center;background:var(--orange-deep);color:#fff;font-size:15px;font-weight:500;border-radius:4px}
.watch{display:flex;align-items:center;gap:14px;font-size:15px;font-weight:500}
.play{width:48px;height:48px;border-radius:50%;border:2px solid #fff;display:flex;align-items:center;justify-content:center}
.play i{width:34px;height:34px;border-radius:50%;background:#fff;display:flex;align-items:center;justify-content:center}

/* sections */
.eyebrow{color:var(--orange);font-size:13px;font-weight:600;letter-spacing:.3px}
.h2{font-weight:700;font-size:44px;line-height:1.2}
.center{left:0;width:1200px;text-align:center}

.works-photo{left:115px;top:829px;width:395px;height:544px;border-radius:50%;background:linear-gradient(160deg,#4c4d50 0%,#9a9a96 45%,#6a6a68 75%,#3a3a3a 100%)}
.step{left:599px;width:500px}
.step h3{font-size:19px;font-weight:600;margin-bottom:12px}
.step .row{display:flex;gap:16px}
.step p{font-size:14px;line-height:24px;color:var(--muted);width:440px}

.card{border-radius:26px;background:var(--panel);text-align:center;padding:24px 30px}
.card.hot{background:linear-gradient(160deg,#f07a38 0%,#e8491d 100%)}
.card .icon{width:108px;height:108px;border-radius:50%;margin:0 auto 22px;display:flex;align-items:center;justify-content:center;border:2px solid var(--orange)}
.card.hot .icon{background:#fff;border:none}
.card h3{font-size:19px;font-weight:600;line-height:28px;margin-bottom:14px}
.card p{font-size:13.5px;line-height:24px;color:#e0e0e0}
.arrow-btn{width:40px;height:40px;border-radius:50%;border:2px solid #fff;display:flex;align-items:center;justify-content:center}

.benefit{width:310px}
.benefit h3{font-size:19px;font-weight:600;margin-bottom:16px}
.benefit .row{display:flex;gap:16px}
.benefit p{font-size:13.5px;line-height:24px;color:var(--muted)}
.chef-photo{left:449px;top:2217px;width:293px;height:454px;border-radius:146px;background:linear-gradient(170deg,#2c2a28 0%,#6e5a48 45%,#c0552a 78%,#2a1a12 100%)}

.quote{left:115px;top:2903px;width:486px;height:269px;border-radius:28px;background:var(--panel);text-align:center;padding:44px 46px}
.stars{display:flex;gap:8px;justify-content:center;margin-bottom:22px}
.quote p{font-style:italic;font-size:15px;line-height:24px;color:#ddd}
.quote .who{font-style:normal;font-weight:600;font-size:14px;margin-top:20px;color:#fff}

.video{left:176px;top:3502px;width:857px;height:366px;border-radius:70px 70px 70px 70px;background:linear-gradient(120deg,#2a1a10 0%,#6b4428 40%,#3b2618 70%,#1d140e 100%)}

.foot-col h4{color:var(--orange);font-size:19px;font-weight:600;margin-bottom:28px}
.foot-col li{list-style:none;font-size:15px;line-height:31.5px;color:#e8e8e8}
.social{width:38px;height:38px;border-radius:50%;border:2px solid #fff}
</style>
</head>
<body>
<div class="page">

  <!-- navigation -->
  <nav class="nav">
    <a class="active"><span>HOME</span></a>
    <a style="left:183px">PRODUCT</a>
    <a style="left:302px">SOLUTIONS</a>
    <a style="left:431px">ROI</a>
    <a class="brand" style="left:508px;top:34px"><span class="mark"></span>KelvaTrix88</a>
    <a style="left:735px">CASE STUDIES</a>
    <a style="left:885px">ABOUT</a>
    <a style="left:981px">CONTACT</a>
  </nav>

  <!-- hero -->
  <div class="abs hero-photo" role="img" aria-label="Dim commercial kitchen with stainless steel cooking stations"></div>
  <svg class="abs" style="left:0;top:620px" width="1200" height="190" viewBox="0 0 1200 190">
    <path d="M260 96 C 600 110 950 120 1140 150 C 1180 135 1198 90 1200 80 L1200 120 C 1190 170 1160 190 1120 178 C 950 140 600 120 260 96 Z" fill="var(--orange-deep)"/>
  </svg>
  <div class="abs hero-card"></div>
  <h1 class="abs hero-title">Meet Tammo</h1>
  <p class="abs hero-sub">— Your New Robotic Chef for High-Volume,<br>Consistent Cooking.</p>
  <p class="abs hero-lead">Increase throughput. Reduce labor. Deliver perfect food every time.</p>
  <a class="abs btn" style="left:395px;top:538px;width:178px;height:48px">Request a Demo</a>
  <div class="abs watch" style="left:593px;top:537px">
    <span class="play"><i><svg width="12" height="14" viewBox="0 0 12 14"><path d="M1 1 L11 7 L1 13Z" fill="#161616"/></svg></i></span>
    Watch Tammo Cook
  </div>

  <!-- how it works -->
  <div class="abs works-photo" role="img" aria-label="Two Tammo cooking robots standing side by side in a kitchen"></div>
  <div class="abs eyebrow" style="left:599px;top:836px">HOW IT WORKS</div>
  <h2 class="abs h2" style="left:597px;top:856px">How Tammo Works</h2>

  <div class="abs step" style="top:934px">
    <h3>Step 1 — Load Ingredients</h3>
    <div class="row"><svg width="30" height="30" viewBox="0 0 30 30"><path d="M6 12a9 9 0 0 1 17-3M24 18a9 9 0 0 1-17 3" stroke="var(--orange)" stroke-width="3" fill="none"/><path d="M23 3v7h-7M7 27v-7h7" stroke="var(--orange)" stroke-width="3" fill="none"/></svg>
    <p>Pour your prepped ingredients directly into Tammo's high-capacity cooking chamber. No special containers, no</p></div>
  </div>
  <div class="abs step" style="top:1041px">
    <h3>Step 2 — Select Recipe</h3>
    <div class="row"><svg width="30" height="30" viewBox="0 0 30 30"><path d="M3 15h24a12 11 0 0 1-24 0Z" fill="var(--orange)"/><path d="M14 13 L24 3" stroke="var(--orange)" stroke-width="3"/></svg>
    <p>Choose from your preset recipes using the intuitive touchscreen interface. Each recipe includes time,</p></div>
  </div>
  <div class="abs step" style="top:1148px">
    <h3>Step 3 — Tammo Cooks</h3>
    <div class="row"><svg width="30" height="30" viewBox="0 0 30 30"><rect x="5" y="11" width="20" height="15" rx="3" fill="var(--orange)"/><rect x="2" y="9" width="26" height="4" rx="2" fill="var(--orange)"/><rect x="13" y="4" width="4" height="5" fill="var(--orange)"/></svg>
    <p>Tammo automatically stirs, heats, rotates, and monitors the entire cooking process from start to finish — delivering</p></div>
  </div>
  <div class="abs step" style="top:1256px">
    <h3>Step 4 — Serve</h3>
    <div class="row"><svg width="30" height="30" viewBox="0 0 30 30"><path d="M4 20a11 11 0 0 1 22 0Z" fill="var(--orange)"/><rect x="2" y="22" width="26" height="4" rx="2" fill="var(--orange)"/><circle cx="15" cy="7" r="2.5" fill="var(--orange)"/></svg>
    <p>Once cooking is done, Tammo dispenses perfectly cooked food — ready to serve or batch into trays for holding, packing, or</p></div>
  </div>

  <!-- who it's for -->
  <div class="abs eyebrow center" style="top:1455px">WHO IT'S FOR</div>
  <h2 class="abs h2 center" style="top:1475px;line-height:52px">Built for Every Industry That Needs<br>Smart Automation</h2>

  <div class="abs arrow-btn" style="left:42px;top:1789px"><svg width="18" height="16" viewBox="0 0 18 16"><path d="M17 8H2M8 2 2 8l6 6" stroke="#fff" stroke-width="2" fill="none"/></svg></div>
  <div class="abs arrow-btn" style="left:1118px;top:1789px"><svg width="18" height="16" viewBox="0 0 18 16"><path d="M1 8h15M10 2l6 6-6 6" stroke="#fff" stroke-width="2" fill="none"/></svg></div>

  <div class="abs card hot" style="left:115px;top:1629px;width:318px;height:356px;border-radius:26px 26px 26px 26px">
    <div class="icon"><svg width="58" height="58" viewBox="0 0 58 58"><rect x="8" y="44" width="22" height="8" fill="var(--orange-deep)"/><path d="M19 44 L24 26 L38 16" stroke="var(--orange-deep)" stroke-width="6" fill="none"/><circle cx="40" cy="14" r="5" fill="var(--orange-deep)"/><rect x="38" y="32" width="16" height="16" fill="var(--orange-deep)"/></svg></div>
    <h3>QSR Restaurants</h3>
    <p>Crush peak-hour demand with faster, consistent batch cooking. Tammo delivers high-throughput cooking with minimal labor—perfect</p>
  </div>
  <div class="abs card" style="left:445px;top:1629px;width:317px;height:356px">
    <div class="icon"><svg width="52" height="52" viewBox="0 0 52 52"><path d="M6 20 L26 6 L46 20 V46 H6Z" fill="var(--orange)"/><rect x="16" y="26" width="20" height="20" fill="var(--panel)"/><rect x="19" y="36" width="6" height="8" fill="var(--orange)"/><rect x="27" y="36" width="6" height="8" fill="var(--orange)"/></svg></div>
    <h3>Fast Casual</h3>
    <p>Improve quality while reducing back-of-house stress.Tammo ensures consistent flavor and texture across all locations, keeping your menu</p>
  </div>
  <div class="abs card" style="left:774px;top:1629px;width:317px;height:356px">
    <div class="icon"><svg width="52" height="52" viewBox="0 0 52 52"><rect x="12" y="6" width="28" height="40" fill="var(--orange)"/><g fill="var(--panel)"><rect x="17" y="12" width="18" height="3"/><rect x="17" y="19" width="18" height="3"/><rect x="17" y="26" width="18" height="3"/><rect x="17" y="33" width="18" height="3"/></g></svg></div>
    <h3>Catering &amp;<br>Commissaries</h3>
    <p>Large-batch cooking... without large staffing. For kitchens producing hundreds of meals per hour, Tammo</p>
  </div>

  <!-- why choose -->
  <div class="abs eyebrow center" style="top:2087px">WHY CHOOSE US</div>
  <h2 class="abs h2 center" style="top:2107px">Why Teams Choose Tammo</h2>
  <div class="abs chef-photo" role="img" aria-label="Chef in whites cooking over a flaming pan"></div>

  <div class="abs benefit" style="left:115px;top:2226px"><h3>Safe, Employee-Friendly</h3><div class="row"><svg width="30" height="30" viewBox="0 0 30 30" style="flex:none"><circle cx="15" cy="15" r="13" stroke="var(--orange)" stroke-width="2" fill="none"/><path d="M9 15h11M15 10l5 5-5 5" stroke="var(--orange)" stroke-width="2" fill="none"/></svg><p>Tammo handles routine tasks 24/7 without breaks, lowering operational and staffing costs across</p></div></div>
  <div class="abs benefit" style="left:115px;top:2385px"><h3>30–50% faster throughput</h3><div class="row"><svg width="30" height="30" viewBox="0 0 30 30" style="flex:none"><circle cx="15" cy="15" r="13" stroke="var(--orange)" stroke-width="2" fill="none"/><path d="M9 15h11M15 10l5 5-5 5" stroke="var(--orange)" stroke-width="2" fill="none"/></svg><p>Tammo handles routine tasks 24/7 without breaks, lowering operational and staffing costs across</p></div></div>
  <div class="abs benefit" style="left:115px;top:2543px"><h3>Health &amp; safety compliance</h3><div class="row"><svg width="30" height="30" viewBox="0 0 30 30" style="flex:none"><circle cx="15" cy="15" r="13" stroke="var(--orange)" stroke-width="2" fill="none"/><path d="M9 15h11M15 10l5 5-5 5" stroke="var(--orange)" stroke-width="2" fill="none"/></svg><p>Tammo handles routine tasks 24/7 without breaks, lowering operational and staffing costs across</p></div></div>
  <div class="abs benefit" style="left:784px;top:2226px"><h3>Labor savings</h3><div class="row"><svg width="30" height="30" viewBox="0 0 30 30" style="flex:none"><circle cx="15" cy="15" r="13" stroke="var(--orange)" stroke-width="2" fill="none"/><path d="M9 15h11M15 10l5 5-5 5" stroke="var(--orange)" stroke-width="2" fill="none"/></svg><p>Tammo handles routine tasks 24/7 without breaks, lowering operational and staffing costs across</p></div></div>
  <div class="abs benefit" style="left:784px;top:2385px"><h3>Zero inconsistency</h3><div class="row"><svg width="30" height="30" viewBox="0 0 30 30" style="flex:none"><circle cx="15" cy="15" r="13" stroke="var(--orange)" stroke-width="2" fill="none"/><path d="M9 15h11M15 10l5 5-5 5" stroke="var(--orange)" stroke-width="2" fill="none"/></svg><p>Tammo handles routine tasks 24/7 without breaks, lowering operational and staffing costs across</p></div></div>
  <div class="abs benefit" style="left:784px;top:2543px"><h3>24/7 Uptime</h3><div class="row"><svg width="30" height="30" viewBox="0 0 30 30" style="flex:none"><circle cx="15" cy="15" r="13" stroke="var(--orange)" stroke-width="2" fill="none"/><path d="M9 15h11M15 10l5 5-5 5" stroke="var(--orange)" stroke-width="2" fill="none"/></svg><p>Tammo handles routine tasks 24/7 without breaks, lowering operational and staffing costs across</p></div></div>

  <!-- testimonials -->
  <div class="abs eyebrow center" style="top:2773px">TESTIMONIALS</div>
  <h2 class="abs h2 center" style="top:2793px">Trusted by Industry Leaders</h2>
  <div class="abs quote">
    <div class="stars">
      <svg width="20" height="20" viewBox="0 0 24 24"><path d="M12 2l3 7 7 .6-5.4 4.7 1.7 7.2L12 17.8 5.7 21.5l1.7-7.2L2 9.6 9 9z" fill="#f7b500"/></svg>
      <svg width="20" height="20" viewBox="0 0 24 24"><path d="M12 2l3 7 7 .6-5.4 4.7 1.7 7.2L12 17.8 5.7 21.5l1.7-7.2L2 9.6 9 9z" fill="#f7b500"/></svg>
      <svg width="20" height="20" viewBox="0 0 24 24"><path d="M12 2l3 7 7 .6-5.4 4.7 1.7 7.2L12 17.8 5.7 21.5l1.7-7.2L2 9.6 9 9z" fill="#f7b500"/></svg>
      <svg width="20" height="20" viewBox="0 0 24 24"><path d="M12 2l3 7 7 .6-5.4 4.7 1.7 7.2L12 17.8 5.7 21.5l1.7-7.2L2 9.6 9 9z" fill="#f7b500"/></svg>
      <svg width="20" height="20" viewBox="0 0 24 24"><path d="M12 2l3 7 7 .6-5.4 4.7 1.7 7.2L12 17.8 5.7 21.5l1.7-7.2L2 9.6 9 9z" fill="#f7b500"/></svg>
    </div>
    <p>“Tammo helped us cut cooking times by nearly 40% during peak hours. The consistency alone has transformed our operations.”</p>
    <p class="who">— OPERATIONS MANAGER, Fast-Casual Chain</p>
  </div>
  <div class="abs" role="img" aria-label="Storefront of a franchise restaurant at night" style="left:625px;top:2903px;width:290px;height:269px;border-radius:28px;background:linear-gradient(180deg,#b8241c 0%,#3a1410 35%,#7a2e18 65%,#1e0f0c 100%)"></div>
  <div class="abs" role="img" aria-label="Exterior sign of a restaurant chain" style="left:939px;top:2903px;width:150px;height:269px;border-radius:28px 0 0 28px;background:linear-gradient(180deg,#8a8a8a 0%,#c2251d 45%,#5e1410 100%)"></div>
  <div class="abs arrow-btn" style="left:548px;top:3205px"><svg width="18" height="16" viewBox="0 0 18 16"><path d="M17 8H2M8 2 2 8l6 6" stroke="#fff" stroke-width="2" fill="none"/></svg></div>
  <div class="abs arrow-btn" style="left:613px;top:3205px;border-color:var(--orange)"><svg width="18" height="16" viewBox="0 0 18 16"><path d="M1 8h15M10 2l6 6-6 6" stroke="var(--orange)" stroke-width="2" fill="none"/></svg></div>

  <!-- video -->
  <h2 class="abs h2 center" style="top:3325px">See Tammo Cook in Action</h2>
  <p class="abs center" style="top:3404px;font-size:17px;line-height:25px;color:#e8e8e8">Watch how Tammo automates high-volume cooking with precision, speed, and<br>consistency—every single batch.</p>
  <svg class="abs" style="left:170px;top:3700px" width="870" height="190" viewBox="0 0 870 190">
    <path d="M6 100 C 20 170 60 176 120 174 L 760 176 C 820 180 860 150 864 60 L 864 100 C 860 170 830 190 770 186 L 120 184 C 50 186 10 170 6 100Z" fill="var(--orange-deep)"/>
  </svg>
  <div class="abs video" role="img" aria-label="Video still of a warm wood-panelled restaurant interior"></div>
  <div class="abs" style="left:578px;top:3660px"><span class="play"><i><svg width="12" height="14" viewBox="0 0 12 14"><path d="M1 1 L11 7 L1 13Z" fill="#161616"/></svg></i></span></div>

  <!-- CTA -->
  <h2 class="abs h2 center" style="top:3961px">Ready to See Tammo Cook Live?</h2>
  <p class="abs center" style="top:4037px;font-size:17px;line-height:25px;color:#e8e8e8">Tammo loads, cooks, stirs, and finishes a complete batch—showing exactly how your<br>kitchen can scale without extra labor.</p>
  <a class="abs btn" style="left:512px;top:4120px;width:178px;height:48px">Book a Demo</a>

  <!-- footer -->
  <svg class="abs" style="left:0;top:4250px" width="1200" height="531" viewBox="0 0 1200 531">
    <path d="M0 80 C 0 60 30 58 70 58 L1120 58 C 1170 58 1190 60 1200 110 L1200 531 L0 531Z" fill="var(--panel-2)"/>
    <path d="M290 54 C 600 40 900 30 1100 20 C 1150 16 1180 40 1196 100 C 1180 56 1150 44 1100 48 C 900 56 600 60 290 54Z" fill="var(--orange-deep)"/>
  </svg>
  <div class="abs brand" style="left:115px;top:4402px;font-size:38px;gap:12px"><span class="mark" style="width:18px;height:18px"></span>KelvaTrix88</div>
  <p class="abs" style="left:115px;top:4462px;font-size:16px;line-height:25px">Smarter Kitchens. Higher<br>Throughput. Consistent Results.</p>
  <div class="abs" style="left:115px;top:4537px;display:flex;gap:8px">
    <span class="social" style="background:var(--orange);border-color:var(--orange)" role="img" aria-label="Social link 1"></span>
    <span class="social" role="img" aria-label="Social link 2"></span>
    <span class="social" role="img" aria-label="Social link 3"></span>
  </div>

  <div class="abs foot-col" style="left:451px;top:4390px"><h4>Product</h4><ul><li>Meet Tammo</li><li>Hardware Features</li><li>Software &amp; AI</li><li>Technical Specs</li><li>Gallery</li><li>Pricing</li></ul></div>
  <div class="abs foot-col" style="left:692px;top:4390px"><h4>Company</h4><ul><li>About Us</li><li>Mission</li><li>Blog / Resources</li><li>Careers</li><li>Press</li><li>Contact</li></ul></div>
  <div class="abs foot-col" style="left:885px;top:4390px"><h4>Solutions</h4><ul><li>Quick-Service Restaurants</li><li>Fast Casual</li><li>Catering &amp; Commissaries</li><li>Ghost Kitchens</li><li>High-Growth Chains</li><li>Case Studies</li></ul></div>

  <div class="abs" style="left:0;top:4727px;width:1200px;height:1px;background:var(--line)"></div>
  <p class="abs center" style="top:4743px;font-size:13px;color:#ddd">© 2025 KelvaTrix88. All Rights Reserved.</p>
</div>
</body>
</html>
```